Brivolt Technologies business card design

We need a business card designed with our new logo. it would be great if the card could communicate it is a technology based company.

Target Market(s)

system integrators

Industry/Entity Type

technology, IOT

Contact Information for Business Card

Name, designation, Address, telephone number, email address

Requirements
Must have
• logo and company name
Nice to have
• something to do with technology

```html
<!DOCTYPE html>
<html lang="en">
<head>
<meta charset="utf-8">
<title>Brivolt Technologies – Business Card</title>
<link href="https://fonts.googleapis.com/css2?family=Open+Sans:wght@400;700&display=swap" rel="stylesheet">
<style>
  :root {
    --backdrop: #3a3a3a;
    --card-white: #ffffff;
    --card-black: #151515;
    --brand-orange: #f7941d;
    --ink-dark: #3b3b3b;
    --ink-mid: #555555;
  }
  * { margin: 0; padding: 0; box-sizing: border-box; }
  html, body {
    width: 1200px; height: 801px; overflow: hidden;
    background: var(--backdrop);
    font-family: "Open Sans", Arial, sans-serif;
  }
  .stage {
    position: relative; width: 1200px; height: 801px;
    display: flex; align-items: center; justify-content: center; gap: 50px;
  }
  .card {
    width: 525px; height: 300px; position: relative;
    border-bottom: 3px solid var(--brand-orange);
    box-shadow: 0 10px 24px rgba(0,0,0,0.35);
  }
  .card--front { background: var(--card-white); }
  .card--back { background: var(--card-black); display: flex; align-items: center; justify-content: center; }

  .wordmark { display: flex; align-items: center; gap: 10px; }
  .wordmark__square { width: 22px; height: 22px; background: var(--brand-orange); flex: none; }
  .wordmark__name {
    font-weight: 700; text-transform: uppercase; line-height: 1.05; letter-spacing: 0.5px;
  }
  .card--front .wordmark { position: absolute; left: 34px; top: 128px; }
  .card--front .wordmark__name { color: var(--ink-dark); font-size: 19px; }
  .card--back .wordmark__name { color: #ffffff; font-size: 30px; }
  .card--back .wordmark__square { width: 32px; height: 32px; }

  .divider {
    position: absolute; left: 262px; top: 62px; width: 2px; height: 180px;
    background: var(--brand-orange);
  }
  .contact { position: absolute; left: 284px; top: 62px; color: var(--ink-mid); font-size: 12px; line-height: 1.5; }
  .contact__name { color: var(--brand-orange); font-weight: 700; font-size: 17px; text-transform: uppercase; line-height: 1.2; }
  .contact__role { margin-bottom: 14px; }
  .contact__address { margin-bottom: 12px; }
  .contact__line { display: flex; align-items: center; gap: 7px; }
  .contact__line svg { width: 11px; height: 11px; flex: none; }
</style>
</head>
<body>
<main class="stage">
  <section class="card card--front">
    <div class="wordmark">
      <span class="wordmark__square"></span>
      <span class="wordmark__name">Brivolt<br>Technologies</span>
    </div>
    <div class="divider"></div>
    <div class="contact">
      <p class="contact__name">Daniel Okafor</p>
      <p class="contact__role">President</p>
      <p class="contact__address">1820 Harbor Crest Dr<br>Seal Cove CA 92700</p>
      <p class="contact__line">
        <svg viewBox="0 0 12 12"><circle cx="6" cy="6" r="6" fill="#f7941d"/><path d="M4 3.2c.4-.3.8 0 1 .5l.3.7c.1.3 0 .5-.2.7l-.3.3c.3.7.9 1.3 1.6 1.6l.3-.3c.2-.2.4-.3.7-.2l.7.3c.5.2.8.6.5 1-.4.6-1 .9-1.7.6C5.3 8 4 6.7 3.5 5.1c-.3-.7 0-1.4.5-1.9z" fill="#fff"/></svg>
        555-240-7180
      </p>
      <p class="contact__line">
        <svg viewBox="0 0 12 12"><rect x="0.5" y="2" width="11" height="8" rx="1" fill="#f7941d"/><path d="M1 2.6 6 6.6l5-4" stroke="#fff" stroke-width="1" fill="none"/></svg>
        info@brivolttech.com
      </p>
      <p class="contact__line">
        <svg viewBox="0 0 12 12"><circle cx="6" cy="6" r="5.5" fill="#f7941d"/><path d="M0.5 6h11M6 0.5c2 2.2 2 8.8 0 11M6 0.5c-2 2.2-2 8.8 0 11" stroke="#fff" stroke-width="0.8" fill="none"/></svg>
        www.brivolttech.com
      </p>
    </div>
  </section>

  <section class="card card--back">
    <div class="wordmark">
      <span class="wordmark__square"></span>
      <span class="wordmark__name">Brivolt<br>Technologies</span>
    </div>
  </section>
</main>
</body>
</html>
```